BrindleStaffing Business Card Design

We are a staffing company finding positions for dedicated nurses and physicians.

Target Market(s)

Business Professionals

Industry/Entity Type

Staffing

Contact Information for Business Card

Gordon Pratley
Chairman
417 39th Avenue South
SAINT PETERSBURG FL 33712
813-555-8036 Mobile
813-555-8036 Fax
gpratley@brindlestaffing.com
www.brindlestaffing.com

Font styles to use
Sans Serif

Colors
fbee3e
f04a50
f37122

Requirements
Must have
• Logo Attached, see colors below. We'd like to see Yellow, Orange and Red.

```html
<!DOCTYPE html>
<html lang="en">
<head>
<meta charset="utf-8">
<title>BrindleStaffing Business Card</title>
<link rel="stylesheet" href="https://fonts.googleapis.com/css2?family=Red+Hat+Display:wght@400;500;700&display=swap">
<style>
  :root {
    --page-bg: #ffffff;
    --brand-orange: #f37122;
    --brand-red: #f04a50;
    --brand-yellow: #fbee3e;
    --card-white: #ffffff;
    --card-edge: #ececec;
    --ink: #1f1f1f;
  }
  * { box-sizing: border-box; margin: 0; padding: 0; }
  html, body {
    width: 1200px; height: 1200px; overflow: hidden;
    background: var(--page-bg);
    font-family: "Red Hat Display", sans-serif;
  }
  .canvas { position: relative; width: 1200px; height: 1200px; }

  .card {
    position: absolute; left: 240px; width: 720px; height: 420px;
    border-radius: 28px; overflow: hidden;
  }
  .card--front { top: 142px; background: var(--brand-orange); }
  .card--back { top: 638px; background: var(--card-white); border: 1px solid var(--card-edge); }

  .wordmark {
    display: flex; align-items: center; gap: 12px;
    font-weight: 700; letter-spacing: -0.5px; white-space: nowrap; line-height: 1;
  }
  .wordmark__dot { flex: none; border-radius: 50%; background: var(--brand-yellow); }

  .card--front .wordmark {
    position: absolute; left: 50%; top: 210px;
    transform: translate(-50%, -50%);
    color: var(--card-white); font-size: 62px;
  }
  .card--front .wordmark__dot { width: 18px; height: 18px; }

  .card--back .wordmark {
    position: absolute; left: 670px; top: 210px;
    transform: translate(-50%, -50%) rotate(-90deg);
    color: var(--brand-orange); font-size: 42px; gap: 10px;
  }
  .card--back .wordmark__dot { width: 13px; height: 13px; }

  .holder { position: absolute; left: 38px; top: 150px; color: var(--ink); }
  .holder__name { color: var(--brand-red); font-size: 31px; font-weight: 500; line-height: 1; }
  .holder__title { margin-top: 10px; font-size: 17px; line-height: 1; }

  .address { position: absolute; left: 38px; top: 237px; font-size: 17px; line-height: 24px; color: var(--ink); font-style: normal; }

  .contacts { position: absolute; left: 38px; top: 297px; list-style: none; color: var(--ink); }
  .contacts li { display: flex; align-items: center; height: 24.5px; font-size: 17px; }
  .contacts svg { width: 13px; height: 13px; margin-right: 13px; fill: var(--brand-orange); flex: none; }
  .contacts svg.icon-line { fill: none; stroke: var(--brand-orange); stroke-width: 1.5; }
</style>
</head>
<body>
<main class="canvas">
  <section class="card card--front" aria-label="Card front">
    <div class="wordmark"><span class="wordmark__dot"></span>BrindleStaffing</div>
  </section>

  <section class="card card--back" aria-label="Card back">
    <div class="holder">
      <h1 class="holder__name">Gordon Pratley</h1>
      <p class="holder__title">Chairman</p>
    </div>
    <address class="address">
      417 39th Avenue South<br>
      SAINT PETERSBURG FL 33712
    </address>
    <ul class="contacts">
      <li>
        <svg viewBox="0 0 16 16" aria-hidden="true"><path d="M3.6 1l2.4 3-1.5 1.6c.8 2 2.4 3.6 4.4 4.4L10.5 8.5l3 2.4-1.3 2.6c-5.6-.4-10.1-4.9-10.5-10.5z"/></svg>
        813-555-4172
      </li>
      <li>
        <svg viewBox="0 0 16 16" aria-hidden="true"><rect x="4" y="1" width="8" height="4"/><rect x="1" y="6" width="14" height="6" rx="1"/><rect x="4" y="10" width="8" height="5" fill="#fff"/><rect x="5" y="11" width="6" height="3"/></svg>
        813-555-8036
      </li>
      <li>
        <svg viewBox="0 0 16 16" aria-hidden="true"><path d="M1 3h14v2L8 9 1 5z"/><path d="M1 6.5l7 4 7-4V13H1z"/></svg>
        gpratley@brindlestaffing.com
      </li>
      <li>
        <svg class="icon-line" viewBox="0 0 16 16" aria-hidden="true"><circle cx="8" cy="8" r="6.2"/><ellipse cx="8" cy="8" rx="2.6" ry="6.2"/><path d="M1.8 8h12.4"/></svg>
        www.brindlestaffing.com
      </li>
    </ul>
    <div class="wordmark"><span class="wordmark__dot"></span>BrindleStaffing</div>
  </section>
</main>
</body>
</html>
```